One page front and back healthcare law brochure

Our small law firm provides legal services to businesses in the health care industry. We would like a single page 8.5x11 front and back brochure that highlights the services we offer. The intent of the brochure is to communicate our professionalism, high work quality, and depth of experience in healthcare law.
Target Market(s)
Doctors, Hospitals, Medical practices, Dental practices, Healthcare clinics, Healthcare tech companies, Healthcare entrepreneurs, Nurses, Med Spas, Pain Management Clinics, Weight Loss Clinics
Industry/Entity Type
Legal, Healthcare
Requirements
Nice to have
- Visually align with https://vennory.law/ and https://vennory.law/health-care/

```html
<!DOCTYPE html>
<html lang="en">
<head>
<meta charset="utf-8">
<title>Vennory Law Healthcare Law Brochure</title>
<link rel="stylesheet" href="https://fonts.googleapis.com/css2?family=Montserrat:ital,wght@0,400;0,500;0,600;0,700;0,800;1,700&family=Oswald:wght@600&display=swap">
<style>
  :root{
    --navy:#1d4fa8;
    --royal:#2160c4;
    --sky:#2b93d9;
    --ink:#3b3f48;
    --paper:#ffffff;
    --backdrop:#eef0f3;
  }
  *{box-sizing:border-box;margin:0;padding:0}
  html,body{width:1200px;height:1200px;overflow:hidden}
  body{background:var(--backdrop);font-family:"Montserrat",sans-serif;color:var(--ink);position:relative}
  .page{position:absolute;top:237px;width:560px;height:725px;background:var(--paper);overflow:hidden;box-shadow:0 2px 10px rgba(0,0,0,.12)}
  .page--front{left:30px}
  .page--back{left:610px}
  .page__stripe{position:absolute;left:0;right:0;bottom:0;height:8px;background:linear-gradient(90deg,var(--royal),var(--sky))}

  .brand{position:absolute;display:flex;align-items:center;gap:8px}
  .brand__mark{width:22px;height:22px;background:var(--navy);border-radius:50%}
  .brand__name{font-weight:700;font-size:24px;color:var(--navy);letter-spacing:.5px;line-height:1}
  .brand__tag{position:absolute;font-size:6.5px;font-weight:600;letter-spacing:1.5px;color:var(--ink);white-space:nowrap}

  .front__texture{position:absolute;left:240px;top:0;width:320px;height:120px;background:linear-gradient(90deg,rgba(255,255,255,0),rgba(215,225,238,.8))}
  .front__photo{position:absolute;left:0;top:75px;width:330px;height:375px;background:linear-gradient(160deg,#f4f7fb 0%,#dfe7f1 55%,#c9d6e6 100%)}
  .front__headline{position:absolute;right:18px;top:112px;text-align:right;font-weight:800;font-size:27px;line-height:1.05;color:var(--navy)}
  .front__headline span{color:var(--sky);display:block}
  .front__intro{position:absolute;left:278px;top:220px;width:272px;padding:10px 12px 10px 18px;background:var(--navy);color:#fff;font-size:6.9px;line-height:1.5;text-align:right;clip-path:polygon(5% 0,100% 0,100% 100%,0 100%)}
  .front__intro-rule{position:absolute;left:300px;top:318px;width:252px;height:3px;background:var(--sky)}
  .front__band{position:absolute;left:8px;top:386px;width:262px;padding:8px 14px;background:var(--royal);color:#fff;font-weight:700;font-size:16px;line-height:1.2;border-radius:0 24px 24px 0}
  .front__col{position:absolute;top:475px;width:245px;font-size:6.9px;line-height:1.5}
  .front__col p+p{margin-top:12px}
  .front__col--left{left:22px}
  .front__col--right{left:303px}

  .contact{position:absolute;width:247px;height:62px;padding:8px 12px;background:var(--navy);color:#fff;border-bottom:4px solid var(--sky)}
  .contact__title{font-weight:700;font-style:italic;font-size:12px;margin-bottom:5px}
  .contact__line{display:flex;align-items:center;gap:4px;font-size:6.6px;line-height:1.6;white-space:nowrap}
  .contact__line svg{width:8px;height:8px;flex:none}
  .page--front .contact{left:303px;top:645px}
  .page--back .contact{left:300px;top:645px}

  .expertise{position:absolute;left:0;top:0;width:278px;height:725px;background:linear-gradient(180deg,var(--royal) 0%,var(--navy) 60%,#3f6bc0 100%)}
  .expertise__title{position:absolute;left:0;top:16px;padding:6px 18px 6px 10px;background:var(--sky);color:#fff;font-weight:700;font-size:15px;line-height:1.1;border-radius:0 22px 22px 0}
  .expertise__list{position:absolute;left:8px;top:78px;width:262px;list-style:none}
  .expertise__item{margin-bottom:14px;color:#fff}
  .expertise__icon{display:flex;align-items:center;gap:6px;margin-bottom:8px}
  .expertise__icon svg{width:13px;height:13px}
  .expertise__icon i{display:block;width:115px;height:1px;background:rgba(255,255,255,.5)}
  .expertise__name{font-weight:600;font-size:11.5px;letter-spacing:.3px;color:#cfe6ff}
  .expertise__text{font-size:6.8px;line-height:1.45}
  .expertise__photo{position:absolute;left:0;top:520px;width:278px;height:205px;background:linear-gradient(180deg,rgba(60,100,190,.5),#8a9fd6 60%,#b7c6ea)}

  .back__visual{position:absolute;left:278px;top:55px;width:282px;height:270px;background:radial-gradient(circle at 40% 35%,#e6f4ff 0%,#9fd0f2 45%,#5aa7dd 100%)}
  .back__visual-fade{position:absolute;left:278px;top:255px;width:282px;height:75px;background:linear-gradient(180deg,rgba(255,255,255,0),#fff)}
  .why{position:absolute;left:315px;top:320px;width:70px;height:70px;border-radius:50%;background:var(--royal);color:#fff;text-align:center;font-family:"Oswald",sans-serif;font-size:13px;line-height:1.05;padding-top:17px}
  .why small{display:block;font-family:"Montserrat",sans-serif;font-size:5.5px;font-weight:700;margin-top:3px}
  .why__arc{position:absolute;left:290px;top:315px}
  .reasons{position:absolute;left:298px;top:425px;width:245px;list-style:none}
  .reasons li{position:relative;padding-left:12px;margin-bottom:12px;font-size:6.9px;line-height:1.45}
  .reasons li svg{position:absolute;left:0;top:1px;width:8px;height:8px}
  .reasons b{color:var(--royal);font-weight:700}
</style>
</head>
<body>

<section class="page page--front">
  <div class="front__texture" role="img" aria-label="Faint pixel grid data texture"></div>
  <div class="front__photo" role="img" aria-label="Photo of a smiling senior doctor in a white coat with stethoscope in a bright clinic"></div>
  <div class="brand" style="left:20px;top:26px">
    <span class="brand__mark"></span>
    <span class="brand__name">VENNORY LAW</span>
  </div>
  <div class="brand__tag" style="left:50px;top:54px">HEALTHCARE BUSINESS COUNSEL</div>

  <h1 class="front__headline">YOUR TRUSTED<br>PARTNER IN<span>HEALTHCARE LAW</span></h1>

  <p class="front__intro">At Vennory Law, our dedicated Healthcare Law Practice Group is committed to safeguarding the interests of healthcare businesses like yours. Our team understands the unique challenges of this highly regulated industry. We are experienced in navigating the complexities of healthcare law to protect your business, allowing you to focus on what you do best: delivering exceptional care.</p>
  <div class="front__intro-rule"></div>

  <h2 class="front__band">PROTECTING &amp;<br>HELPING YOUR BUSINESS<br>GROW</h2>

  <div class="front__col front__col--left">
    <p>Whether you're starting a new business or managing an established enterprise, the focus of your attention and energy is on developing and commercializing your practice, products, and/or services. Due to time constraints and the overwhelming amount of work your business requires, proper legal planning sometimes takes a back seat. We can help. Vennory Law seeks to relieve the stress and anxiety associated with unaddressed legal issues by handling these challenges and allowing our clients to focus on growing their companies.</p>
    <p>Our Healthcare Law practice encompasses a wide range of services. We guide clients through the proper establishment of new businesses, and the myriad issues that arise as companies interact with the public, other companies, regulatory bodies, and the government. We help make sure businesses are correctly organized and comply with state and federal laws, rules, and regulations pertaining to raising capital, acquiring other businesses or assets, protecting patient information, complying with health law regulations and statutes, and adding and removing owners.</p>
  </div>
  <div class="front__col front__col--right">
    <p>Buying a healthcare business, cementing a strategic partnership, and executing an exit event are all fraught with pitfalls and unexpected risks. When a deal or contract needs to get negotiated, documented, and closed - we excel. We fight to get the right deal terms for our clients and offer creative solutions to help navigate these minefields and achieve a successful result.</p>
    <p>We work with all forms of businesses including partnerships, limited liability companies (LLCs), and corporations. Regardless of the type of business, it is imperative that the potential legal threats and obstacles the business may face are properly addressed.</p>
  </div>

  <div class="contact">
    <div class="contact__title">Contact Us Today:</div>
    <div class="contact__line"><svg viewBox="0 0 10 10"><circle cx="5" cy="5" r="5" fill="#fff"/><circle cx="5" cy="4.3" r="1.6" fill="#1d4fa8"/></svg>4180 Harbor Point Drive, Suite 310 Davidson, NC, 28036</div>
    <div class="contact__line"><svg viewBox="0 0 10 10"><circle cx="5" cy="5" r="5" fill="#fff"/><path d="M3.3 2.6l1 1-.6.8c.4.8 1 1.4 1.8 1.8l.8-.6 1 1-.7.9C4.6 7.3 2.7 5.4 2.5 3.3z" fill="#1d4fa8"/></svg>(704) 555-0142
      <svg viewBox="0 0 10 10" style="margin-left:8px"><circle cx="5" cy="5" r="5" fill="#fff"/><rect x="2.6" y="3.3" width="4.8" height="3.4" fill="#1d4fa8"/></svg>info@vennory.law</div>
  </div>
  <div class="page__stripe"></div>
</section>

<section class="page page--back">
  <div class="expertise">
    <h2 class="expertise__title">EXAMPLES OF<br>OUR EXPERTISE:</h2>
    <ul class="expertise__list">
      <li class="expertise__item">
        <div class="expertise__icon"><svg viewBox="0 0 12 12"><path d="M6 1l5 4v6H1V5z" fill="#cfe6ff"/><path d="M5.3 5h1.4v1.3H8v1.4H6.7V9H5.3V7.7H4V6.3h1.3z" fill="#1d4fa8"/></svg><i></i></div>
        <div class="expertise__name">MEDICAL PRACTICES:</div>
        <p class="expertise__text">Navigating the intricate landscape of healthcare regulations, regulatory compliance, and business legal issues. We ensure that your practice operates smoothly while avoiding costly legal pitfalls.</p>
      </li>
      <li class="expertise__item">
        <div class="expertise__icon"><svg viewBox="0 0 12 12"><ellipse cx="6" cy="8" rx="5" ry="2.5" fill="#cfe6ff"/><circle cx="6" cy="4" r="2" fill="#cfe6ff"/></svg><i></i></div>
        <div class="expertise__name">MED SPAS:</div>
        <p class="expertise__text">Guiding med spas through confusing and ever-changing regulations, licensing, and compliance issues while ensuring their operations are legally sound.</p>
      </li>
      <li class="expertise__item">
        <div class="expertise__icon"><svg viewBox="0 0 12 12"><rect x="2" y="1" width="8" height="10" rx="1.5" fill="none" stroke="#cfe6ff" stroke-width="1.2"/><path d="M6 7.5L4.2 5.7a1 1 0 0 1 1.8-1 1 1 0 0 1 1.8 1z" fill="#cfe6ff"/></svg><i></i></div>
        <div class="expertise__name">MEDICAL DEVICE COMPANIES:</div>
        <p class="expertise__text">Providing counsel on regulatory compliance, intellectual property, product liability, and contracts to help device manufacturers succeed in a competitive marketplace.</p>
      </li>
      <li class="expertise__item">
        <div class="expertise__icon"><svg viewBox="0 0 12 12"><rect x="1" y="2" width="10" height="7" fill="none" stroke="#cfe6ff" stroke-width="1.1"/><path d="M2 6h2l1-2 1.5 3L8 5h2" fill="none" stroke="#cfe6ff" stroke-width="1"/></svg><i></i></div>
        <div class="expertise__name">MEDICAL SOFTWARE COMPANIES:</div>
        <p class="expertise__text">Addressing the unique legal needs of software companies in healthcare, including data privacy, cybersecurity, and regulatory compliance.</p>
      </li>
      <li class="expertise__item">
        <div class="expertise__icon"><svg viewBox="0 0 12 12"><circle cx="6" cy="2.5" r="1.6" fill="#cfe6ff"/><rect x="3.5" y="4.5" width="5" height="6.5" rx="1.5" fill="#cfe6ff"/></svg><i></i></div>
        <div class="expertise__name">WEIGHT LOSS AND PAIN<br>MANAGEMENT CLINICS:</div>
        <p class="expertise__text">Offering guidance and support on compliance, licensing, and patient care and safety to ensure exceptional care while adhering to strict regulatory standards.</p>
      </li>
    </ul>
    <div class="expertise__photo" role="img" aria-label="Group photo of smiling healthcare professionals in scrubs and white coats"></div>
  </div>

  <div class="brand" style="left:304px;top:18px">
    <span class="brand__mark" style="width:17px;height:17px"></span>
    <span class="brand__name" style="font-size:19px">VENNORY LAW</span>
  </div>
  <div class="brand__tag" style="left:329px;top:40px;font-size:5.5px">HEALTHCARE BUSINESS COUNSEL</div>

  <div class="back__visual" role="img" aria-label="Blue digital healthcare visual with glowing medical cross and network lines"></div>
  <div class="back__visual-fade"></div>

  <svg class="why__arc" width="270" height="90" viewBox="0 0 270 90" aria-hidden="true">
    <path d="M40 4a40 40 0 1 0 60 52h170" fill="none" stroke="#2160c4" stroke-width="1.5"/>
  </svg>
  <div class="why">WHY<br>CHOOSE<small>VENNORY LAW?</small></div>

  <ul class="reasons">
    <li><svg viewBox="0 0 10 10"><rect x=".5" y=".5" width="9" height="9" fill="none" stroke="#2160c4"/><path d="M2.5 5l2 2 3.5-4" fill="none" stroke="#2160c4" stroke-width="1.2"/></svg><b>Industry-Focused:</b><br>Our deep understanding of the healthcare sector enables us to provide tailored legal solutions.</li>
    <li><svg viewBox="0 0 10 10"><rect x=".5" y=".5" width="9" height="9" fill="none" stroke="#2160c4"/><path d="M2.5 5l2 2 3.5-4" fill="none" stroke="#2160c4" stroke-width="1.2"/></svg><b>Experienced Team: Our HIPAA certified:</b><br>attorneys have extensive experience in healthcare law, delivering effective counsel and representation.</li>
    <li><svg viewBox="0 0 10 10"><rect x=".5" y=".5" width="9" height="9" fill="none" stroke="#2160c4"/><path d="M2.5 5l2 2 3.5-4" fill="none" stroke="#2160c4" stroke-width="1.2"/></svg><b>Proactive Approach:</b><br>We anticipate challenges before they arise, providing strategic advice to safeguard your business.</li>
    <li><svg viewBox="0 0 10 10"><rect x=".5" y=".5" width="9" height="9" fill="none" stroke="#2160c4"/><path d="M2.5 5l2 2 3.5-4" fill="none" stroke="#2160c4" stroke-width="1.2"/></svg><b>Comprehensive Services:</b><br>From compliance to drafting legal documents to dispute resolution, we offer end-to-end legal support for most healthcare law needs.</li>
  </ul>

  <div class="contact">
    <div class="contact__title">Contact Us Today:</div>
    <div class="contact__line"><svg viewBox="0 0 10 10"><circle cx="5" cy="5" r="5" fill="#fff"/><circle cx="5" cy="4.3" r="1.6" fill="#1d4fa8"/></svg>4180 Harbor Point Drive, Suite 310 Davidson, NC, 28036</div>
    <div class="contact__line"><svg viewBox="0 0 10 10"><circle cx="5" cy="5" r="5" fill="#fff"/><path d="M3.3 2.6l1 1-.6.8c.4.8 1 1.4 1.8 1.8l.8-.6 1 1-.7.9C4.6 7.3 2.7 5.4 2.5 3.3z" fill="#1d4fa8"/></svg>(704) 555-0142
      <svg viewBox="0 0 10 10" style="margin-left:8px"><circle cx="5" cy="5" r="5" fill="#fff"/><rect x="2.6" y="3.3" width="4.8" height="3.4" fill="#1d4fa8"/></svg>info@vennory.law</div>
  </div>
  <div class="page__stripe"></div>
</section>

</body>
</html>
```